Business Card Design Project

I need a business card designed from scratch. I have an existing logo that I can upload in Illustrator for modification or redesign.

The Company is called Query Lanterns http://querylanterns.com.au and we provide Search Engine Optimization services to Australian businesses. The current logo signifies an increase in visitors, profits etc...

There are no restrictions as to the redesign - colours, style etc are all open to change.

Cards will be full colour and one sided printed at http://www.cardmoxel.com.au so check their requirements for file format and sizes etc.

I will expect all original files upon completion of project.

Target Market(s)

Any business with a web site looking to improve their search engine rankings

Industry/Entity Type

Business

Requirements
Must have
• I like modern, sleek designs. Clean, not fussy, uncluttered.

```html
<!DOCTYPE html>
<html lang="en">
<head>
<meta charset="utf-8">
<title>Query Lanterns – Business Card</title>
<link rel="stylesheet" href="https://fonts.googleapis.com/css2?family=Open+Sans:wght@400;600;700;800&display=swap">
<style>
  :root {
    --brand-blue: #1b6fb5;
    --deep-blue: #175f9f;
    --brand-yellow: #f7c81e;
    --text-grey: #4a4a4a;
    --muted-grey: #6b6b6b;
    --divider: #c9c9c9;
    --card: #ffffff;
    --backdrop: #ecebe8;
  }
  * { margin: 0; padding: 0; box-sizing: border-box; }
  html, body {
    width: 1200px; height: 460px; overflow: hidden;
    background: var(--backdrop);
    font-family: "Open Sans", Arial, sans-serif;
  }
  .canvas { position: relative; width: 1200px; height: 460px; }

  .card {
    position: absolute; top: 75px;
    width: 542px; height: 309px;
    background: var(--card);
    overflow: hidden;
    box-shadow: 0 1px 3px rgba(0,0,0,0.12);
  }
  .card--front { left: 44px; }
  .card--back { left: 614px; }

  /* Front */
  .brand {
    position: absolute; left: 38px; top: 124px;
    display: flex; align-items: center; gap: 10px;
  }
  .brand__dot {
    width: 18px; height: 18px; border-radius: 50%;
    background: var(--brand-yellow);
  }
  .brand__name {
    font-weight: 800; font-size: 29px; line-height: 1;
    color: var(--brand-blue); letter-spacing: -0.5px;
  }
  .divider {
    position: absolute; left: 294px; top: 75px;
    width: 1px; height: 139px; background: var(--divider);
  }
  .person {
    position: absolute; left: 307px; top: 79px;
    white-space: nowrap;
  }
  .person__name { font-weight: 700; font-size: 17px; color: var(--brand-blue); }
  .person__title { font-size: 13px; color: var(--text-grey); margin-left: 3px; }
  .contacts {
    position: absolute; left: 309px; top: 114px;
    list-style: none;
  }
  .contacts li {
    display: flex; align-items: center; gap: 6px;
    font-size: 13px; line-height: 18px; color: var(--text-grey);
  }
  .contacts svg { width: 9px; height: 9px; fill: var(--brand-blue); flex: none; }

  .band { position: absolute; left: 0; bottom: 0; width: 542px; height: 70px; }
  .address {
    position: absolute; left: 42px; bottom: 20px;
    font-size: 13px; color: #ffffff;
  }

  /* Back */
  .back-brand {
    position: absolute; left: 0; right: 0; top: 108px;
    display: flex; justify-content: center; align-items: center; gap: 12px;
  }
  .back-brand__dot {
    width: 22px; height: 22px; border-radius: 50%;
    background: var(--brand-yellow);
  }
  .back-brand__name {
    font-weight: 800; font-size: 34px; color: var(--brand-blue);
    letter-spacing: -0.5px;
  }
  .back-url {
    position: absolute; left: 0; right: 0; top: 229px;
    text-align: center; font-size: 13px; letter-spacing: 2.6px;
    color: var(--muted-grey);
  }
  .back-url__domain { color: var(--brand-blue); }
</style>
</head>
<body>
<main class="canvas">

  <section class="card card--front" aria-label="Card front">
    <div class="brand">
      <span class="brand__dot"></span>
      <span class="brand__name">Query Lanterns</span>
    </div>

    <div class="divider"></div>

    <p class="person">
      <span class="person__name">Your Name</span>
      <span class="person__title">Title</span>
    </p>

    <ul class="contacts">
      <li>
        <svg viewBox="0 0 10 10" aria-hidden="true"><path d="M2 0.5l2 2-1 1.2c.6 1.3 1.5 2.2 2.8 2.8l1.2-1 2 2-1.3 1.8C4 9 1 6 .5 1.8z"/></svg>
        098 765 4321
      </li>
      <li>
        <svg viewBox="0 0 10 10" aria-hidden="true"><rect x="2.5" y="0" width="5" height="10" rx="1"/></svg>
        098 765 4321
      </li>
      <li>
        <svg viewBox="0 0 10 10" aria-hidden="true"><path d="M0 2h10v6H0z M0 2l5 3.5L10 2" /></svg>
        enquiry@querylanterns.com.au
      </li>
      <li>
        <svg viewBox="0 0 10 10" aria-hidden="true"><circle cx="5" cy="5" r="4.5"/></svg>
        www.querylanterns.com.au
      </li>
    </ul>

    <svg class="band" viewBox="0 0 542 70" preserveAspectRatio="none" aria-hidden="true">
      <path d="M0 20 C150 -4 360 0 542 30 L542 34 C360 6 150 4 0 24 Z" fill="var(--brand-yellow)"/>
      <path d="M0 24 C150 4 360 6 542 34 L542 70 L0 70 Z" fill="var(--brand-blue)"/>
    </svg>
    <p class="address">00Floor Street, City Name, State Name, Contry Name</p>
  </section>

  <section class="card card--back" aria-label="Card back">
    <div class="back-brand">
      <span class="back-brand__dot"></span>
      <span class="back-brand__name">Query Lanterns</span>
    </div>
    <p class="back-url">www.<span class="back-url__domain">querylanterns</span>.com.au</p>
  </section>

</main>
</body>
</html>
```